Letterhead and matching envelope design for a dental office

We need a new stationary design, letterhead and envelope #10, for a dental office in Denver area. We are called Bright Harbor Dental. We want a simple and minimalistic design but not a boring design. I wish to have one good point that makes it look professional. I have attached our logo. Feel free to use either one. I want the design for letterhead and envelope look like a "matching pair" but not look the same. The envelope doesn't have to be white and it will have an address window on bottom left.

Target Market(s)

everyone who visits dentist (adults)

Industry/Entity Type

Dental

Font styles to use
Other font styles liked:
• close to font on logo or something that matches well

Requirements
Must have
• professional
• simple, minimalistic
• unique point that stands out
Nice to have
• matching but not same design for letterhead and envelope
Should not have
• not look like all the other boring designs
• no flowery, distracting feats

```html
<!DOCTYPE html>
<html lang="en">
<head>
<meta charset="utf-8">
<title>Bright Harbor Dental – Envelope #10</title>
<link rel="stylesheet" href="https://fonts.googleapis.com/css2?family=Source+Sans+3:wght@400;600&display=swap">
<style>
  :root {
    --green: #3bb54a;
    --green-pale: #b9e3be;
    --motif: #eef7ee;
    --ink: #1f1f1f;
    --paper: #ffffff;
    --backdrop: #e9e9e9;
  }
  * { box-sizing: border-box; margin: 0; padding: 0; }
  html, body { width: 1200px; height: 928px; overflow: hidden; }
  body {
    background: var(--backdrop);
    font-family: "Source Sans 3", Arial, sans-serif;
    position: relative;
  }
  .envelope {
    position: absolute;
    width: 690px;
    height: 300px;
    background: var(--paper);
    overflow: hidden;
    box-shadow: 0 2px 6px rgba(0,0,0,0.12);
  }
  .envelope--back { left: 450px; top: 110px; }
  .envelope--front { left: 60px; top: 500px; }

  .motif {
    position: absolute;
    left: 200px;
    top: 40px;
    width: 300px;
    height: 190px;
    border-radius: 50%;
    background: radial-gradient(ellipse at center, var(--motif) 0%, var(--motif) 55%, rgba(238,247,238,0) 72%);
  }

  .bands { position: absolute; left: 0; right: 0; bottom: 0; height: 60px; }
  .band-pale {
    position: absolute; left: 0; top: 8px; width: 66%; height: 6px;
    background: var(--green-pale);
  }
  .band-green {
    position: absolute; left: 0; right: 0; top: 18px; height: 9px;
    background: var(--green);
  }
  .web {
    position: absolute; right: 44px; top: 30px;
    font-size: 15px; font-weight: 600; color: var(--green); letter-spacing: 0.2px;
  }
  .web-tab {
    position: absolute; right: 0; top: 40px; width: 36px; height: 7px;
    background: var(--green-pale);
  }

  .flap { position: absolute; left: 0; top: 0; width: 690px; height: 230px; }
  .flap-name {
    position: absolute; left: 440px; top: 58px; width: 110px;
    display: flex; align-items: center; gap: 6px;
    color: var(--paper); font-size: 12px; font-weight: 600;
    letter-spacing: 1.5px; text-transform: uppercase; line-height: 1.2;
  }
  .dot { flex: none; width: 10px; height: 10px; border-radius: 50%; background: currentColor; }

  .brand {
    position: absolute; left: 30px; top: 30px; width: 120px;
    display: flex; align-items: center; gap: 7px;
    color: var(--green); font-size: 13px; font-weight: 600;
    letter-spacing: 1.8px; text-transform: uppercase; line-height: 1.2;
  }
  .sender {
    position: absolute; left: 18px; top: 166px;
    font-size: 14px; line-height: 1.25; color: var(--ink);
  }
  .sender-name { color: var(--green); }
  .contact {
    position: absolute; left: 208px; top: 200px;
    font-size: 14px; line-height: 1.35; color: var(--ink);
    list-style: none;
  }
  .contact li { display: flex; align-items: center; gap: 5px; }
  .contact svg { width: 12px; height: 12px; flex: none; }
</style>
</head>
<body>

<section class="envelope envelope--back" aria-label="Envelope back">
  <div class="motif" role="img" aria-label="Faint brand motif"></div>
  <svg class="flap" viewBox="0 0 690 230" aria-hidden="true">
    <path d="M0 0 H690 V190 C690 215 670 228 640 222 L440 168 C400 158 380 150 330 138 L0 40 Z" fill="var(--green)"/>
  </svg>
  <div class="flap-name"><span class="dot"></span><span>Bright Harbor Dental</span></div>
  <div class="bands">
    <span class="band-pale"></span>
    <span class="band-green"></span>
    <span class="web">www.brightharbordental.com</span>
    <span class="web-tab"></span>
  </div>
</section>

<section class="envelope envelope--front" aria-label="Envelope front">
  <div class="motif" role="img" aria-label="Faint brand motif"></div>
  <div class="brand"><span class="dot"></span><span>Bright Harbor Dental</span></div>
  <address class="sender" style="font-style:normal">
    <div class="sender-name">Bright Harbor Dental</div>
    <div>2815 Lakeview Ave,</div>
    <div>Suite 210 Arvada, CO 80002</div>
  </address>
  <ul class="contact">
    <li>
      <svg viewBox="0 0 12 12" aria-hidden="true"><circle cx="6" cy="6" r="6" fill="var(--green)"/><path d="M4 3.2l1 1.3-.6.7c.4.9 1 1.5 1.9 1.9l.7-.6 1.3 1-.6 1.2C5.8 8.6 3.4 6.2 3.2 3.8z" fill="#fff"/></svg>
      <span>720-555-0146</span>
    </li>
    <li>
      <svg viewBox="0 0 12 12" aria-hidden="true"><circle cx="6" cy="6" r="6" fill="var(--green)"/><rect x="3" y="4" width="6" height="4.2" fill="#fff"/><path d="M3 4l3 2.3L9 4" fill="none" stroke="var(--green)" stroke-width=".7"/></svg>
      <span>info@brightharbordental.com</span>
    </li>
  </ul>
  <div class="bands">
    <span class="band-pale"></span>
    <span class="band-green"></span>
    <span class="web">www.brightharbordental.com</span>
    <span class="web-tab"></span>
  </div>
</section>

</body>
</html>
```